I need a 6 x 11 postcard created that adheres to the design templates of the Federated parcel bureau. It will be mailed to scholars to encourage them to attend and present papers at the Marrowgate Indie International Film Festival's "Frame, Signal, and Score Conference." It must be provocative and engaging like a film festival poster. One option would be to high light the glitz of Hollywood and the appeal of the beach/shoreline in Long Beach but that's just one idea and I would love for the designer to just come with something original. It should be artistically compelling in that it would cause someone to keep the postcard even if they didn't care about the event. It must stand out in the mail and on a bulletin board.

You DO NOT have to use logo that I included and you do not have to stick with color schemes that are on logo.

My notes are in red on the document that includes the text.

the front can be portrait or landscape but back must be landscape. Also, designs submitted should include front and back.

You do not have to use the logo I included. If you do use the logo you can change the colors to fit your design Ideas.

The postcard will be sent to scholars who study and write about film, television, music, and digital media. We are inviting them to participate in a conference by selling them hollywood and the beaches of southern california.

Festival

• The design must be bold and inventive. Either ultramodern or just artistically appealing. The words 'Frame, Signal, and Score Conference" and "Call for Papers, Films, and Exhibitors Now Open!" must be clear on the front. It should be bright and inviting or classically beautiful (e.g. black and white).

It must match the Federated Parcel Bureau design requirements for 6 x 11 postcards
• This has got to be taken seriously by some very creative and intelligent people who love art, film, etc.

```html
<!DOCTYPE html>
<html lang="en">
<head>
<meta charset="utf-8">
<title>Frame, Signal, and Score Conference — Postcard Front and Back</title>
<link rel="stylesheet" href="https://fonts.googleapis.com/css2?family=Antonio:wght@100;200;300&display=swap">
<style>
  :root {
    --page-bg: #e8e8e6;
    --card-paper: #f4f4f2;
    --rule: #4a4a4a;
    --sea-deep: #2b2629;
    --sea-violet: #4e4257;
    --sea-teal: #5f9598;
    --foam: #bcd8d5;
    --disc: rgba(22, 21, 24, 0.9);
    --ink-light: #ecefee;
    --ink-soft: #b9c2c1;
  }
  html, body {
    margin: 0;
    width: 1200px;
    height: 675px;
    overflow: hidden;
    background: var(--page-bg);
  }
  .postcard {
    position: absolute;
    top: 190px;
    width: 540px;
    height: 295px;
    box-shadow: 0 2px 10px rgba(0,0,0,0.14);
  }
  .postcard-front { left: 40px; }
  .postcard-back { left: 620px; background: var(--card-paper); }
  .postcard svg { display: block; }
  .type {
    font-family: "Antonio", "Arial Narrow", sans-serif;
    fill: var(--ink-light);
    text-anchor: middle;
    text-transform: uppercase;
  }
  .headline { font-weight: 100; font-size: 46px; letter-spacing: 1px; }
  .call { font-weight: 200; font-size: 23px; letter-spacing: 1.5px; }
  .web { font-weight: 300; font-size: 12px; letter-spacing: 2px; fill: var(--ink-soft); text-transform: lowercase; }
  .place { font-weight: 100; font-size: 32px; letter-spacing: 1px; }
  .date { font-weight: 300; font-size: 13px; letter-spacing: 2px; fill: var(--ink-soft); }
  .deadline { font-weight: 100; font-size: 32px; letter-spacing: 1px; }
  .back-rule { stroke: var(--rule); stroke-width: 2; fill: none; }
</style>
</head>
<body>

<section class="postcard postcard-front" aria-label="Postcard front">
  <svg width="540" height="295" viewBox="0 0 1100 600">
    <defs>
      <linearGradient id="sea-base" x1="0" y1="0" x2="1" y2="1">
        <stop offset="0" stop-color="var(--sea-violet)"/>
        <stop offset="0.5" stop-color="var(--sea-deep)"/>
        <stop offset="1" stop-color="var(--sea-violet)"/>
      </linearGradient>
      <linearGradient id="surf-band" x1="0" y1="1" x2="1" y2="0">
        <stop offset="0" stop-color="var(--foam)" stop-opacity="0"/>
        <stop offset="0.3" stop-color="var(--sea-teal)" stop-opacity="0.55"/>
        <stop offset="0.5" stop-color="var(--foam)" stop-opacity="0.6"/>
        <stop offset="0.7" stop-color="var(--sea-teal)" stop-opacity="0.45"/>
        <stop offset="1" stop-color="var(--foam)" stop-opacity="0"/>
      </linearGradient>
    </defs>

    <g class="sea-photo" role="img" aria-label="Photograph of breaking ocean surf in teal and violet tones">
      <rect width="1100" height="600" fill="url(#sea-base)"/>
      <rect width="1100" height="600" fill="url(#surf-band)"/>
    </g>

    <g class="discs">
      <circle cx="560" cy="255" r="180" fill="var(--disc)"/>
      <circle cx="220" cy="300" r="100" fill="var(--disc)"/>
      <circle cx="890" cy="205" r="90" fill="var(--disc)"/>
      <circle cx="700" cy="48" r="36" fill="var(--disc)"/>
      <circle cx="760" cy="520" r="40" fill="var(--disc)"/>
      <circle cx="85" cy="265" r="30" fill="var(--disc)"/>
      <circle cx="330" cy="505" r="60" fill="var(--disc)"/>
      <circle cx="470" cy="555" r="14" fill="var(--disc)"/>
      <circle cx="1040" cy="420" r="22" fill="var(--disc)"/>
    </g>

    <g class="conference-title">
      <text class="type headline" x="560" y="180">Frame, Signal,</text>
      <text class="type headline" x="560" y="228">and Score</text>
      <text class="type headline" x="560" y="276">Conference</text>
      <text class="type call" x="560" y="316">Call for Papers,</text>
      <text class="type call" x="560" y="343">Films and Exhibitors</text>
      <text class="type call" x="560" y="370">Now Open!</text>
      <text class="type web" x="560" y="396">framesignalscore.example</text>
    </g>

    <g class="event-place">
      <text class="type date" x="220" y="262">September 15–17, 2016</text>
      <text class="type place" x="220" y="300">Marrowgate</text>
      <text class="type place" x="220" y="338">California</text>
    </g>

    <g class="paper-deadline">
      <text class="type deadline" x="890" y="192">Paper</text>
      <text class="type deadline" x="890" y="228">Deadline</text>
      <text class="type date" x="890" y="252">April 1, 2016</text>
    </g>
  </svg>
</section>

<section class="postcard postcard-back" aria-label="Postcard back">
  <svg width="540" height="295" viewBox="0 0 1100 600">
    <line class="back-rule divider" x1="560" y1="60" x2="560" y2="540"/>
    <rect class="back-rule stamp-box" x="900" y="50" width="140" height="140"/>
    <g class="address-lines">
      <line class="back-rule" x1="620" y1="300" x2="1040" y2="300"/>
      <line class="back-rule" x1="620" y1="360" x2="1040" y2="360"/>
      <line class="back-rule" x1="620" y1="420" x2="1040" y2="420"/>
      <line class="back-rule" x1="620" y1="480" x2="1040" y2="480"/>
    </g>
  </svg>
</section>

</body>
</html>
```